We need a business card design for a new company located in Brampton Ontario Canada. Our goal is to promote companies to use our service as an "External Program Management " firm taking their industrial product concepts " from prototype to production." We would like to use blue and yellow as our colors. Our skills include finding suppliers for prototype parts and developing them into supplying not only prototypes but the final production parts as well for our customer base.
Industry/Entity Type
Business
Contact Information for Business Card
Derek Namsby
Sales Manager
KOLVEN Solutions Inc.
14 Pinemarsh Lane
Brampton, Ontario L7P 2K9
Canada
Phone: 905-481-2976
Fax: 905-481-2976
website: www.kolvensolutions-example.com
Email: derek@kolvensolutions-example.com
Look and feel
Each slider illustrates characteristics of the customer's brand and the style your logo design should communicate.

```html
<!DOCTYPE html>
<html lang="en">
<head>
<meta charset="utf-8">
<title>KOLVEN Solutions Inc – Business Card</title>
<link rel="stylesheet" href="https://fonts.googleapis.com/css2?family=Marcellus+SC&display=swap">
<style>
  :root {
    --page-bg: #e4e6ea;
    --card-white: #ffffff;
    --brand-blue: #1f2fd6;
    --accent-grey: #a9abb0;
    --accent-yellow: #f5c400;
    --ink-dark: #2a2a2a;
    --ink-light: #ffffff;
  }
  * { box-sizing: border-box; margin: 0; padding: 0; }
  html, body {
    width: 1200px;
    height: 900px;
    overflow: hidden;
    background: var(--page-bg);
    font-family: "Marcellus SC", "Trajan Pro", serif;
  }
  .sheet {
    width: 1200px;
    height: 900px;
    display: flex;
    flex-direction: column;
    align-items: center;
    justify-content: center;
    gap: 60px;
  }
  .card {
    position: relative;
    width: 600px;
    height: 343px;
    border-radius: 26px;
    background: var(--card-white);
    overflow: hidden;
    box-shadow: 0 6px 18px rgba(0, 0, 0, 0.12);
  }
  .card-art {
    position: absolute;
    inset: 0;
    width: 100%;
    height: 100%;
  }
  .wordmark {
    position: absolute;
    color: var(--brand-blue);
    line-height: 1;
    text-align: left;
  }
  .wordmark-name {
    display: block;
    font-size: 58px;
    letter-spacing: 2px;
  }
  .wordmark-sub {
    display: block;
    font-size: 27px;
    letter-spacing: 0.5px;
    margin-top: 4px;
  }
  .card-front .wordmark { top: 62px; right: 46px; }
  .card-back .wordmark { top: 108px; left: 150px; }

  .contact-list {
    position: absolute;
    left: 26px;
    top: 108px;
    list-style: none;
    color: var(--ink-light);
    font-size: 11px;
    line-height: 14px;
  }
  .contact-item {
    display: flex;
    align-items: flex-start;
    gap: 6px;
    white-space: nowrap;
  }
  .contact-icon {
    width: 9px;
    height: 9px;
    margin-top: 2px;
    flex: none;
  }
  .contact-icon.spacer { visibility: hidden; }

  .holder {
    position: absolute;
    left: 372px;
    top: 222px;
    width: 190px;
    text-align: center;
    color: var(--ink-dark);
  }
  .holder-name { font-size: 22px; letter-spacing: 0.5px; }
  .holder-title { font-size: 18px; margin-top: 4px; letter-spacing: 0.5px; }
</style>
</head>
<body>
<main class="sheet">

  <section class="card card-front" aria-label="Business card front">
    <svg class="card-art" viewBox="0 0 600 343" aria-hidden="true">
      <path d="M150,0 L190,0 C255,80 270,200 360,250 C440,292 530,286 600,282 L600,294 C520,298 425,300 345,262 C255,212 235,90 150,0 Z" fill="var(--accent-grey)"/>
      <path d="M170,0 L176,0 C240,90 262,215 352,268 C430,312 530,306 600,302 L600,306 C520,310 425,318 345,274 C258,222 232,90 170,0 Z" fill="var(--accent-yellow)"/>
      <path d="M0,0 L160,0 C222,90 240,215 330,268 C415,318 525,312 600,310 L600,343 L0,343 Z" fill="var(--brand-blue)"/>
    </svg>

    <div class="wordmark">
      <span class="wordmark-name">KOLVEN</span>
      <span class="wordmark-sub">Solutions Inc</span>
    </div>

    <ul class="contact-list">
      <li class="contact-item">
        <svg class="contact-icon" viewBox="0 0 10 10"><circle cx="5" cy="5" r="5" fill="#fff"/><path d="M5 2 C3.4 2 2.8 3.3 3.2 4.4 L5 8 L6.8 4.4 C7.2 3.3 6.6 2 5 2 Z" fill="var(--brand-blue)"/></svg>
        <span>14 Pinemarsh Lane,</span>
      </li>
      <li class="contact-item">
        <svg class="contact-icon spacer" viewBox="0 0 10 10"></svg>
        <span>Brampton, Ontario L7P 2K9</span>
      </li>
      <li class="contact-item">
        <svg class="contact-icon spacer" viewBox="0 0 10 10"></svg>
        <span>Canada</span>
      </li>
      <li class="contact-item">
        <svg class="contact-icon" viewBox="0 0 10 10"><circle cx="5" cy="5" r="5" fill="#fff"/><path d="M3 2.5 L4.2 2.5 L4.6 4 L3.9 4.6 C4.3 5.4 4.7 5.8 5.4 6.1 L6 5.4 L7.5 5.8 L7.5 7 C5 7.3 2.7 5 3 2.5 Z" fill="var(--brand-blue)"/></svg>
        <span>T: 905-481-2976</span>
      </li>
      <li class="contact-item">
        <svg class="contact-icon" viewBox="0 0 10 10"><circle cx="5" cy="5" r="5" fill="#fff"/><rect x="2.5" y="3.5" width="5" height="3.5" fill="var(--brand-blue)"/><rect x="3.5" y="2.2" width="3" height="1.3" fill="var(--brand-blue)"/></svg>
        <span>F: 905-481-2976</span>
      </li>
      <li class="contact-item">
        <svg class="contact-icon" viewBox="0 0 10 10"><circle cx="5" cy="5" r="5" fill="#fff"/><rect x="2.3" y="3" width="5.4" height="4" fill="var(--brand-blue)"/><path d="M2.3 3 L5 5.2 L7.7 3" stroke="#fff" stroke-width="0.6" fill="none"/></svg>
        <span>derek@kolvensolutions-example.com</span>
      </li>
      <li class="contact-item">
        <svg class="contact-icon" viewBox="0 0 10 10"><circle cx="5" cy="5" r="5" fill="#fff"/><circle cx="5" cy="5" r="2.6" fill="none" stroke="var(--brand-blue)" stroke-width="0.8"/><path d="M2.4 5 H7.6 M5 2.4 V7.6" stroke="var(--brand-blue)" stroke-width="0.6"/></svg>
        <span>www.kolvensolutions-example.com</span>
      </li>
    </ul>

    <div class="holder">
      <p class="holder-name">Derek Namsby</p>
      <p class="holder-title">Sales Manager</p>
    </div>
  </section>

  <section class="card card-back" aria-label="Business card back">
    <div class="wordmark">
      <span class="wordmark-name">KOLVEN</span>
      <span class="wordmark-sub">Solutions Inc</span>
    </div>
  </section>

</main>
</body>
</html>
```